Business Card Design for Occupational Medicine Start Up Company

We need to design a professional business card. We are a healthcare company providing occupational medicine services to blue collar industries. We are professional, efficient and high quality service providers.

Target Market(s)

Blue Collar Industry: Shipbuilding, Ports, Trucking Companies; The Executives and Safety Officers for these companies

Industry/Entity Type

Healthcare

Contact Information for Business Card

Logo, Name, Title, Email, Phone

Other font styles liked:
• Please match our Brand Guide

Requirements
Must have
• Our Company Colors and Logo

```html
<!DOCTYPE html>
<html lang="en">
<head>
<meta charset="utf-8">
<title>Crewline Clinics – Business Card</title>
<link rel="stylesheet" href="https://fonts.googleapis.com/css2?family=Montserrat:wght@400;700;800&family=Lato:wght@400;700&display=swap">
<style>
  :root {
    --stage: #1e1e20;
    --navy: #2b3487;
    --emboss: #3a47d6;
    --white: #ffffff;
    --cyan: #27a6df;
    --orange: #f3ad45;
    --ink: #2b3487;
  }
  * { box-sizing: border-box; margin: 0; padding: 0; }
  html, body { width: 1200px; height: 1015px; overflow: hidden; }
  body {
    background: var(--stage);
    position: relative;
    font-family: "Lato", Arial, sans-serif;
  }
  .card {
    position: absolute;
    left: 250px;
    width: 700px;
    height: 400px;
    overflow: hidden;
    background: var(--navy);
    box-shadow: 0 14px 30px rgba(0,0,0,.55);
  }
  .card--back { top: 60px; }
  .card--front { top: 545px; }

  /* back side */
  .back-brand {
    position: absolute;
    inset: 0;
    display: flex;
    align-items: center;
    justify-content: center;
    gap: 18px;
  }
  .back-brand__dot {
    width: 54px; height: 54px;
    border-radius: 50%;
    background: var(--emboss);
  }
  .back-brand__name {
    font-family: "Montserrat", Arial, sans-serif;
    font-weight: 800;
    font-size: 40px;
    letter-spacing: 2px;
    color: var(--emboss);
    line-height: 1.05;
  }

  /* front side */
  .front-shapes { position: absolute; inset: 0; }
  .holder {
    position: absolute;
    left: 42px;
    top: 64px;
    color: var(--white);
  }
  .holder__name {
    font-family: "Montserrat", Arial, sans-serif;
    font-size: 25px;
    letter-spacing: .5px;
    line-height: 1.1;
  }
  .holder__name strong { font-weight: 800; }
  .holder__name span { font-weight: 400; }
  .holder__title { font-size: 18px; margin-top: 2px; }

  .address {
    position: absolute;
    left: 80px;
    top: 212px;
    color: var(--white);
    font-size: 17px;
    line-height: 1.25;
  }
  .contacts {
    position: absolute;
    left: 80px;
    top: 282px;
    list-style: none;
    color: var(--white);
    font-size: 17px;
    line-height: 1.4;
  }
  .contacts li { display: flex; align-items: center; gap: 8px; }
  .contacts svg { width: 17px; height: 17px; flex: none; }

  .front-brand {
    position: absolute;
    left: 420px;
    top: 100px;
    display: flex;
    align-items: center;
    gap: 14px;
  }
  .front-brand__dot {
    width: 44px; height: 44px;
    border-radius: 50%;
    background: var(--cyan);
  }
  .front-brand__name {
    font-family: "Montserrat", Arial, sans-serif;
    font-weight: 800;
    font-size: 30px;
    letter-spacing: 1.5px;
    color: var(--ink);
    line-height: 1.05;
  }
</style>
</head>
<body>

<section class="card card--back" aria-label="Card back">
  <div class="back-brand">
    <div class="back-brand__dot"></div>
    <div class="back-brand__name">CREWLINE<br>CLINICS</div>
  </div>
</section>

<section class="card card--front" aria-label="Card front">
  <svg class="front-shapes" viewBox="0 0 700 400" aria-hidden="true">
    <rect width="700" height="400" fill="var(--navy)"/>
    <circle cx="512" cy="125" r="245" fill="var(--cyan)"/>
    <circle cx="528" cy="140" r="243" fill="var(--orange)"/>
    <circle cx="522" cy="128" r="235" fill="var(--white)"/>
  </svg>

  <div class="holder">
    <p class="holder__name"><strong>DANIEL</strong> <span>MARSH</span></p>
    <p class="holder__title">Managing Director</p>
  </div>

  <p class="address">18 Harbor Road<br>Portside, 40217</p>

  <ul class="contacts">
    <li>
      <svg viewBox="0 0 24 24"><path fill="#fff" d="M6.6 10.8a15.1 15.1 0 0 0 6.6 6.6l2.2-2.2c.3-.3.7-.4 1-.2 1.1.4 2.3.6 3.6.6.6 0 1 .4 1 1V20c0 .6-.4 1-1 1A17 17 0 0 1 3 4c0-.6.4-1 1-1h3.5c.6 0 1 .4 1 1 0 1.3.2 2.5.6 3.6.1.3 0 .7-.2 1z"/></svg>
      041-555 208 316
    </li>
    <li>
      <svg viewBox="0 0 24 24"><path fill="#fff" d="M2 5h20v14H2zm2 2v.5l8 5 8-5V7zm0 2.8V17h16V9.8l-8 5z"/></svg>
      hello@crewlineclinics.com
    </li>
    <li>
      <svg viewBox="0 0 24 24" fill="none" stroke="#fff" stroke-width="2"><circle cx="12" cy="12" r="9"/><path d="M3 12h18M12 3c3 3 3 15 0 18M12 3c-3 3-3 15 0 18"/></svg>
      www.crewlineclinics.com
    </li>
  </ul>

  <div class="front-brand">
    <div class="front-brand__dot"></div>
    <div class="front-brand__name">CREWLINE<br>CLINICS</div>
  </div>
</section>

</body>
</html>
```